Beacon Advisory Website

I currently have a website www.beaconadvisoryinc.com. We are a IT Consulting Company. Our website will pretty much tell out our services. I am looking to enhance my website and make it look more professional. Looking for very classy and Contemporary look and design for my website.

It Company

```html
<!DOCTYPE html>
<html lang="en">
<head>
<meta charset="utf-8">
<title>Beacon Advisory</title>
<link href="https://fonts.googleapis.com/css2?family=Lato:wght@400;700;900&family=Oswald:wght@400&family=Exo+2:wght@600&display=swap" rel="stylesheet">
<style>
:root{
  --brand:#0a68b0;
  --brand-dark:#07549a;
  --navy:#0b1a2e;
  --ink:#222;
  --footer:#222222;
  --card:#141414;
  --white:#fff;
  --muted:#cfcfcf;
  --rule:#444;
}
*{margin:0;padding:0;box-sizing:border-box}
html,body{width:1200px;height:1045px;overflow:hidden}
body{font-family:"Lato",sans-serif;color:var(--ink);background:var(--white);position:relative}
.topbar{position:absolute;left:0;top:0;width:1200px;height:33px;background:var(--brand)}
.topbar-phone{position:absolute;left:790px;top:0;height:33px;display:flex;align-items:center;gap:8px;color:var(--white);font-weight:700;font-size:16px}
.topbar-social{position:absolute;left:962px;top:0;display:flex}
.topbar-social span{width:35px;height:33px;background:#1a7fcc;border-left:1px solid var(--brand);display:flex;align-items:center;justify-content:center}
.topbar-social span i{width:12px;height:12px;background:var(--white);display:block;border-radius:2px}
.header{position:absolute;left:0;top:33px;width:1200px;height:83px;background:var(--white)}
.brand{position:absolute;left:100px;top:22px;display:flex;align-items:center;gap:10px}
.brand-mark{width:40px;height:40px;border-radius:50%;background:var(--brand)}
.brand-name{font-weight:900;font-size:24px;color:var(--brand);letter-spacing:.5px}
.nav{position:absolute;left:460px;top:28px;display:flex;align-items:center}
.nav-home{width:36px;display:flex;justify-content:center}
.nav a{font-size:16px;color:#222;text-decoration:none;padding:0 11px;border-left:1px solid #ccc;line-height:22px;letter-spacing:.3px}
.hero{position:absolute;left:0;top:116px;width:1200px;height:642px;background:radial-gradient(circle at 62% 38%,#2d6fb0 0%,#16406c 30%,#0c1f35 65%,#0a1524 100%)}
.hero-title{position:absolute;left:100px;top:148px;font-family:"Oswald",sans-serif;font-size:29px;line-height:36px;color:var(--white);width:460px}
.hero-cta{position:absolute;left:100px;top:278px;width:249px;height:52px;background:var(--brand-dark);border:2px solid var(--white);color:var(--white);font-weight:900;font-size:20px;display:flex;align-items:center;justify-content:center}
.card{position:absolute;top:414px;width:303px;height:180px;background:var(--card);border-radius:4px;box-shadow:0 8px 14px rgba(0,0,0,.5)}
.card-tab{position:absolute;left:-6px;top:6px;height:37px;width:274px;background:var(--white);clip-path:polygon(0 0,100% 0,92% 100%,0 100%);font-size:18px;color:#222;padding:8px 0 0 15px;letter-spacing:.3px}
.card-tab b{font-weight:400;color:var(--brand)}
.card-icon{position:absolute;left:19px;top:62px;width:77px;height:77px;border-radius:50%;background:var(--brand);border:2px solid var(--white);display:flex;align-items:center;justify-content:center}
.card-text{position:absolute;left:112px;top:56px;width:180px;font-size:12.5px;line-height:16.5px;color:var(--white)}
.card-list{position:absolute;left:118px;top:56px;list-style:none;font-size:13px;color:var(--white)}
.card-list li{line-height:23px}
.card-list li::before{content:"»";margin-right:12px;font-size:11px}
.news-title{font-family:Arial,sans-serif;font-weight:700;font-size:13px;margin-bottom:8px}
.news-body{font-family:Arial,sans-serif;font-size:12px;line-height:18px;padding-left:5px}
.card-more{position:absolute;right:26px;top:154px;font-size:12.5px;color:var(--white);text-decoration:underline}
.footer{position:absolute;left:0;top:758px;width:1200px;height:243px;background:var(--footer);color:var(--white)}
.col-title{font-family:"Exo 2",sans-serif;font-size:18px;letter-spacing:.5px;padding-bottom:8px;border-bottom:1px dotted #555}
.col{position:absolute;top:26px}
.links{list-style:none;margin-top:10px;font-size:13px}
.links li{line-height:23px}
.links li::before{content:"»";margin-right:14px;font-size:11px}
.divider{position:absolute;top:55px;width:1px;height:140px;background:var(--rule)}
.contact-row{display:flex;gap:8px;font-size:13px;line-height:18px;margin-top:14px}
.contact-row b{font-weight:700}
.field{width:216px;height:26px;background:var(--white);color:#555;font-size:12px;padding:6px 8px;margin-top:8px}
.field.tall{height:43px}
.submit{margin-top:11px;width:64px;height:26px;background:var(--brand);font-family:"Exo 2",sans-serif;font-size:14px;display:flex;align-items:center;justify-content:center}
.footer-brand{position:absolute;left:920px;top:58px;display:flex;align-items:center;gap:8px}
.footer-brand .brand-mark{background:#888;width:34px;height:34px}
.footer-brand .brand-name{color:#9a9a9a;font-size:20px}
.footer-social{position:absolute;left:937px;top:143px;display:flex;gap:8px}
.footer-social span{width:31px;height:31px;border-radius:50%}
.copyright{position:absolute;left:0;top:1001px;width:1200px;height:44px;background:var(--brand);color:var(--white);font-size:12.5px;display:flex;align-items:center;justify-content:center}
</style>
</head>
<body>
<div class="topbar">
  <div class="topbar-phone">
    <svg width="14" height="16" viewBox="0 0 14 16"><path d="M3 1l3 3-2 2c1 2 3 4 5 5l2-2 3 3-2 3C6 15 0 9 1 3z" fill="#fff"/></svg>
    +1 (555) 014 2290
  </div>
  <div class="topbar-social" aria-label="Social links">
    <span><i></i></span><span><i></i></span><span><i></i></span><span><i></i></span>
  </div>
</div>

<header class="header">
  <div class="brand"><span class="brand-mark"></span><span class="brand-name">BEACON ADVISORY</span></div>
  <nav class="nav">
    <span class="nav-home"><svg width="22" height="20" viewBox="0 0 22 20"><path d="M11 1L1 10h3v9h5v-6h4v6h5v-9h3z" fill="#0a68b0"/></svg></span>
    <a>COMPANY</a><a>SERVICES</a><a>SOLUTIONS</a><a>RESOURCES</a><a>CAREER</a><a>CONTACT US</a>
  </nav>
</header>

<section class="hero" role="img" aria-label="Businessman touching a glowing blue network of gears">
  <h1 class="hero-title">We Will Delivers Highest Level Of Quality Consultants And Services For The Lowest Cost Of Ownership</h1>
  <div class="hero-cta">GET STARTED WITH US</div>

  <article class="card" style="left:100px">
    <div class="card-tab"><b>ABOUT</b> BEACON ADVISORY</div>
    <div class="card-icon"><svg width="40" height="40" viewBox="0 0 40 40"><ellipse cx="25" cy="12" rx="13" ry="9" fill="none" stroke="#fff" stroke-width="2.5"/><circle cx="12" cy="22" r="5" fill="#fff"/><path d="M3 38c0-8 4-11 9-11s9 3 9 11z" fill="#fff"/></svg></div>
    <p class="card-text">Today's IT market is a dynamic, fast-paced industry, with ever-increasing demands. Meeting these demands for over 25 years, Beacon Advisory...</p>
    <span class="card-more">Read More</span>
  </article>

  <article class="card" style="left:449px">
    <div class="card-tab"><b>OUR</b> SERVICES</div>
    <div class="card-icon"><svg width="44" height="44" viewBox="0 0 44 44"><g fill="#fff" transform="translate(22 22)"><rect x="-4" y="-20" width="8" height="40"/><rect x="-4" y="-20" width="8" height="40" transform="rotate(45)"/><rect x="-4" y="-20" width="8" height="40" transform="rotate(90)"/><rect x="-4" y="-20" width="8" height="40" transform="rotate(135)"/><circle r="14"/></g><circle cx="22" cy="22" r="6" fill="#0a68b0"/></svg></div>
    <ul class="card-list"><li>Technology</li><li>Business</li><li>Application</li><li>Developement</li></ul>
    <span class="card-more">Read More</span>
  </article>

  <article class="card" style="left:798px">
    <div class="card-tab"><b>INDUSTRIAL</b> NEWS</div>
    <div class="card-icon"><svg width="42" height="36" viewBox="0 0 42 36"><rect x="3" y="3" width="36" height="30" rx="5" fill="none" stroke="#fff" stroke-width="3.5"/><rect x="10" y="10" width="9" height="8" fill="#fff"/><rect x="22" y="10" width="11" height="3" fill="#fff"/><rect x="22" y="16" width="11" height="3" fill="#fff"/><rect x="10" y="22" width="23" height="3" fill="#fff"/></svg></div>
    <div class="card-text" style="left:98px;width:200px">
      <div class="news-title">✔ Lorem ipsum dolor smit amet</div>
      <div class="news-body">consectetuer adipiscing litmk, sed amet diam nonummy nibh euismod tincidun nt ut reetml dolore aliq.</div>
    </div>
    <span class="card-more">Read More</span>
  </article>
</section>

<footer class="footer">
  <div class="col" style="left:100px;width:128px">
    <div class="col-title">Quick Links</div>
    <ul class="links"><li>Home</li><li>Company</li><li>Services</li><li>Solutions</li><li>Resources</li><li>Career</li><li>Contact Us</li></ul>
  </div>
  <span class="divider" style="left:267px"></span>

  <div class="col" style="left:317px;width:194px">
    <div class="col-title">Contact Details</div>
    <div class="contact-row"><svg width="10" height="14" viewBox="0 0 10 14"><path d="M5 0a5 5 0 015 5c0 4-5 9-5 9S0 9 0 5a5 5 0 015-5z" fill="#fff"/><circle cx="5" cy="5" r="2" fill="#222"/></svg><div><b>HEAD OFFICE</b><br>420 Harbor Lane<br>Suite 110<br>Eastbrook, NJ 07001</div></div>
    <div class="contact-row"><svg width="12" height="14" viewBox="0 0 14 16"><path d="M3 1l3 3-2 2c1 2 3 4 5 5l2-2 3 3-2 3C6 15 0 9 1 3z" fill="#fff"/></svg><b>+1 (555) 014 2290</b></div>
    <div class="contact-row"><svg width="14" height="10" viewBox="0 0 14 10"><rect width="14" height="10" fill="#fff"/><path d="M0 0l7 6 7-6" fill="none" stroke="#222" stroke-width="1.3"/></svg>info@beaconadvisory.com</div>
  </div>
  <span class="divider" style="left:551px"></span>

  <div class="col" style="left:601px;width:228px">
    <div class="col-title">Quick Inquiry</div>
    <div class="field" style="margin-top:16px">Name</div>
    <div class="field">Email</div>
    <div class="field tall">Message</div>
    <div class="submit">Submit</div>
  </div>
  <span class="divider" style="left:869px"></span>

  <div class="footer-brand"><span class="brand-mark"></span><span class="brand-name">BEACON ADVISORY</span></div>
  <div class="footer-social" aria-label="Social links">
    <span style="background:#3b5998"></span><span style="background:#1da1f2"></span><span style="background:#e0312a"></span><span style="background:#dd4b39"></span>
  </div>
</footer>

<div class="copyright">Copyright © 2016 Beacon Advisory Inc.&nbsp; All Rights Reserved.</div>
</body>
</html>
```